Business card design for a dynamic IT consulting company

We need a business card design for a young firm, specialized in the Telecommunications/Consulting industry. The name of the company is Quindor and Partners Business Consulting Ltd. (Short name: Quindor and Partnes)
Quindor = solve read reverse, so we aim to be uncomplicated and solution-oriented. The small pipe in our logo is also related to the word solve. So we need a new business card design, which is simple, eye catching and something non traditional (I would probably prefer a square shaped design rather than a rectangle, but open for suggestions). Attached our logo.

Target Market(s)

Usually our customers are Tier1 Telecoms providers (Q-Netra, Palorix, etc) and their executives.

Industry/Entity Type

Business

Contact Information for Business Card

Name: Bence Tolnavari
Email: b.tolnavari@quindor.hu
Web: www.quindor.hu
Mobile: +36 30 518 2769
Title: Managing Director

Optional:
Company name: Quindor and Partners Ltd.
Address: 1087 Budapest, Tolvenka str. 28/C, Hungary

Font styles to use
Other font styles liked:
• helveticaneue_medium, Prime Regular are used now.

Colors

Designer to choose colors to be used in the design.

Requirements
Must have
• I would like to have a 2 sided design.
Nice to have
• I thought if we make the logo a bit bigger (without the company name), that could go to the back with the company name below. I though, if the pipe in the logo is somehow touchable on the business card, would be nice and unique.

```html
<!DOCTYPE html>
<html lang="en">
<head>
<meta charset="utf-8">
<title>Quindor &amp; Partners – Business Card</title>
<link rel="stylesheet" href="https://fonts.googleapis.com/css2?family=Roboto:wght@300;400;500;700&display=swap">
<style>
  :root {
    --stage: #9b9b9b;
    --card-light: #ffffff;
    --card-dark: #141414;
    --ink: #4a4a4a;
    --ink-soft: #5c5c5c;
    --name-blue: #1a78c2;
    --accent-magenta: #b0208f;
    --accent-cyan: #1ea3dc;
    --accent-grey: #6a6a6a;
    --rule: #b5b5b5;
    --on-dark: #f2f2f2;
  }
  * { margin: 0; padding: 0; box-sizing: border-box; }
  html, body {
    width: 1200px; height: 1134px; overflow: hidden;
    background: var(--stage);
    font-family: "Roboto", Arial, sans-serif;
  }
  .sheet { position: relative; width: 1200px; height: 1134px; }

  .card {
    position: absolute; top: 389px;
    width: 382px; height: 382px;
    border-radius: 14px;
  }
  .card--front { left: 207px; background: var(--card-light); color: var(--ink); text-align: center; }
  .card--back  { left: 650px; background: var(--card-dark); }

  .wordmark {
    display: flex; align-items: center; justify-content: center; gap: 10px;
    font-weight: 300; font-size: 29px; letter-spacing: 0.2px; white-space: nowrap;
  }
  .wordmark__dot { width: 12px; height: 12px; background: var(--accent-magenta); }
  .card--front .wordmark { position: absolute; top: 36px; left: 0; right: 0; color: var(--ink); }
  .card--back .wordmark { position: absolute; top: 174px; left: 0; right: 0; color: var(--on-dark); font-size: 31px; }

  .person { position: absolute; top: 112px; left: 0; right: 0; }
  .person__name { font-weight: 700; font-size: 28px; color: var(--name-blue); line-height: 1.2; }
  .person__title { font-weight: 400; font-size: 17px; color: var(--ink-soft); margin-top: 1px; }

  .contact-icons {
    position: absolute; top: 198px; left: 0; right: 0;
    display: flex; justify-content: center; gap: 7px;
  }
  .contact-icons svg { width: 20px; height: 20px; display: block; }

  .contact { position: absolute; top: 227px; left: 0; right: 0; font-size: 15.5px; line-height: 22.5px; color: var(--ink); }
  .divider { position: absolute; top: 303px; left: 143px; width: 96px; height: 2px; background: var(--rule); }
  .address { position: absolute; top: 316px; left: 0; right: 0; font-size: 15.5px; line-height: 23px; color: var(--ink); }
</style>
</head>
<body>
<main class="sheet">

  <section class="card card--front" aria-label="Card front">
    <div class="wordmark"><span class="wordmark__dot"></span><span>Quindor &amp; Partners</span></div>

    <div class="person">
      <h1 class="person__name">Bence Tolnavari</h1>
      <p class="person__title">Managing Director</p>
    </div>

    <div class="contact-icons">
      <svg viewBox="0 0 20 20" aria-label="Phone">
        <circle cx="10" cy="10" r="10" fill="var(--accent-magenta)"/>
        <path d="M7 5.5c.5-.4 1-.3 1.3.2l.9 1.6c.2.4.1.8-.2 1.1l-.6.5c.5 1.1 1.3 1.9 2.4 2.4l.5-.6c.3-.3.7-.4 1.1-.2l1.6.9c.5.3.6.8.2 1.3l-.6.7c-.6.6-1.6.7-2.5.2-2-1-3.6-2.6-4.6-4.6-.5-.9-.4-1.9.2-2.5z" fill="#fff"/>
      </svg>
      <svg viewBox="0 0 20 20" aria-label="Email">
        <circle cx="10" cy="10" r="10" fill="var(--accent-cyan)"/>
        <rect x="5" y="6.5" width="10" height="7" rx="1" fill="#fff"/>
        <path d="M5.3 7l4.7 3.6L14.7 7" fill="none" stroke="var(--accent-cyan)" stroke-width="1"/>
      </svg>
      <svg viewBox="0 0 20 20" aria-label="Website">
        <circle cx="10" cy="10" r="10" fill="var(--accent-grey)"/>
        <circle cx="10" cy="10" r="5" fill="none" stroke="#fff" stroke-width="1.2"/>
        <ellipse cx="10" cy="10" rx="2.2" ry="5" fill="none" stroke="#fff" stroke-width="1"/>
        <path d="M5 10h10" stroke="#fff" stroke-width="1"/>
      </svg>
    </div>

    <div class="contact">
      <p>801.472.3096</p>
      <p>b.tolnavari@quindor.hu</p>
      <p>www.quindor.hu</p>
    </div>
    <div class="divider"></div>
    <address class="address" style="font-style:normal">
      <p>1087 Budapest,</p>
      <p>Tolvenka str. 28/C, Hungary</p>
    </address>
  </section>

  <section class="card card--back" aria-label="Card back">
    <div class="wordmark"><span class="wordmark__dot"></span><span>Quindor &amp; Partners</span></div>
  </section>

</main>
</body>
</html>
```